Local fast-growing company in the service sector

We are looking for a modern business card design, which should also appear on our letterheads

Target Market(s)

Private and industrial sectors

Contact Information for Business Card

Vorname Name
Kellberger Str. 18
73614 Lindental
Tel.: 07146-839214-0
Name@agentur-kvtl.de

Colors
9d9d9d
919191
aaaaaa

Requirements
Must have
• The logo (file) in silver

```html
<!DOCTYPE html>
<html lang="de">
<head>
<meta charset="utf-8">
<title>KVTL Visitenkarte</title>
<link rel="stylesheet" href="https://fonts.googleapis.com/css2?family=Quicksand:wght@500;700&display=swap">
<style>
  :root {
    --page-bg: #e4e4e4;
    --card-center: #3b3b3b;
    --card-edge: #222222;
    --silver: #aaaaaa;
    --silver-light: #c4c4c4;
    --text-light: #dcdcdc;
    --icon: #9d9d9d;
  }
  * { margin: 0; padding: 0; box-sizing: border-box; }
  html, body {
    width: 1200px;
    height: 576px;
    overflow: hidden;
    background: var(--page-bg);
    font-family: "Quicksand", sans-serif;
  }
  .canvas {
    position: relative;
    width: 1200px;
    height: 576px;
  }
  .card {
    position: absolute;
    top: 138px;
    height: 292px;
    border-radius: 11px;
    background: radial-gradient(ellipse at 50% 40%, var(--card-center) 0%, var(--card-edge) 80%);
    overflow: hidden;
  }
  .card--front { left: 82px; width: 485px; }
  .card--back { left: 602px; width: 480px; }

  .brand {
    position: absolute;
    color: var(--silver-light);
    font-weight: 700;
    letter-spacing: 2px;
    line-height: 1;
  }
  .card--front .brand {
    left: 0; right: 0;
    top: 114px;
    text-align: center;
    font-size: 64px;
  }
  .card--back .brand {
    right: 26px;
    top: 112px;
    font-size: 48px;
  }

  .holder-name {
    position: absolute;
    left: 23px;
    top: 46px;
    font-size: 17px;
    font-weight: 700;
    letter-spacing: 2px;
    color: var(--silver);
  }

  .contact-list {
    position: absolute;
    left: 23px;
    top: 196px;
    list-style: none;
    font-size: 13.5px;
    font-weight: 500;
    color: var(--text-light);
    letter-spacing: 0.4px;
  }
  .contact-list li {
    display: flex;
    align-items: center;
    height: 17px;
  }
  .contact-icon {
    width: 9px;
    height: 9px;
    margin-right: 11px;
    fill: var(--icon);
  }
  .contact-address {
    position: absolute;
    left: 23px;
    top: 251px;
    font-size: 13.5px;
    font-weight: 500;
    color: var(--text-light);
    letter-spacing: 0.4px;
  }
</style>
</head>
<body>
<main class="canvas">
  <section class="card card--front" aria-label="Vorderseite">
    <div class="brand">KVTL</div>
  </section>

  <section class="card card--back" aria-label="Rückseite">
    <div class="holder-name">VORNAME NAME</div>
    <div class="brand">KVTL</div>

    <ul class="contact-list">
      <li>
        <svg class="contact-icon" viewBox="0 0 10 10" aria-hidden="true">
          <path d="M1 3.2C1 2 2 1.5 5 1.5S9 2 9 3.2L7.4 3.8 7 3C6 2.7 4 2.7 3 3L2.6 3.8ZM2.6 4.6H7.4L8.6 8.5H1.4ZM5 5.4A1.3 1.3 0 1 0 5 8 1.3 1.3 0 1 0 5 5.4Z"/>
        </svg>
        07146-839214-0
      </li>
      <li>
        <svg class="contact-icon" viewBox="0 0 10 10" aria-hidden="true">
          <path d="M0.5 2H9.5V8.5H0.5ZM1.3 2.6 5 5.6 8.7 2.6Z" fill-rule="evenodd"/>
        </svg>
        Name@agentur-kvtl.de
      </li>
      <li>
        <svg class="contact-icon" viewBox="0 0 10 10" aria-hidden="true">
          <circle cx="5" cy="5" r="4.3" fill="none" stroke="#9d9d9d" stroke-width="1"/>
          <ellipse cx="5" cy="5" rx="1.8" ry="4.3" fill="none" stroke="#9d9d9d" stroke-width="0.8"/>
          <path d="M0.7 5H9.3" stroke="#9d9d9d" stroke-width="0.8"/>
        </svg>
        www.agentur-kvtl.de
      </li>
    </ul>
    <div class="contact-address">Kellberger Str. 18 73614 Lindental</div>
  </section>
</main>
</body>
</html>
```